Business Card Design Project

We need a new fresh business card for our business. There are multiple services we offer and we need a fresh corporate card that represents us better. We start from cleaning carpet and tiles, to upholstery and curtains, to completely clean all contents and building materials after a fire, or completely dry out a home or business after a major or minor flood event. We are open to all concepts as we want to create a new look, maybe even logo, signage, vehicle signage, uniforms.
We are open to new colours etc.

Go to www.brolvaquincare.com.au for current logo and all other past ideas

Target Market(s)

Everyone is our possible client but we are targeting more coorporate

Industry/Entity Type

Building

```html
<!DOCTYPE html>
<html lang="en">
<head>
<meta charset="utf-8">
<title>Brolvaquin Care – Business Card</title>
<link rel="stylesheet" href="https://fonts.googleapis.com/css2?family=Open+Sans:wght@400;600;700&display=swap">
<style>
  :root {
    --page-bg: #e9e9ec;
    --card-white: #f7f7f8;
    --brand-blue: #1d5c9e;
    --brand-pink: #e0237f;
    --text-light: #ffffff;
    --text-soft: #e6eef8;
  }
  * { margin: 0; padding: 0; box-sizing: border-box; }
  html, body {
    width: 1200px;
    height: 900px;
    overflow: hidden;
    background: var(--page-bg);
    font-family: "Open Sans", Arial, sans-serif;
  }
  .business-card {
    position: absolute;
    left: 150px;
    top: 190px;
    width: 900px;
    height: 520px;
    border-radius: 56px;
    overflow: hidden;
    background: linear-gradient(135deg, #ffffff 0%, var(--card-white) 55%, #e9e9eb 100%);
    box-shadow: 0 14px 34px rgba(0, 0, 0, 0.18);
  }
  .card-shapes {
    position: absolute;
    inset: 0;
    width: 900px;
    height: 520px;
  }
  .contact-panel {
    position: absolute;
    left: 58px;
    top: 82px;
    color: var(--text-light);
  }
  .person-name {
    font-size: 34px;
    font-weight: 700;
    line-height: 1.15;
  }
  .person-title {
    font-size: 25px;
    font-weight: 400;
    color: var(--text-soft);
    margin-left: 14px;
  }
  .office-address {
    margin-top: 58px;
    margin-left: 44px;
    font-size: 21px;
    line-height: 1.45;
    font-style: normal;
    color: var(--text-soft);
  }
  .contact-list {
    list-style: none;
    margin-top: 50px;
    margin-left: 76px;
    font-size: 20px;
    line-height: 1.55;
    color: var(--text-soft);
  }
  .contact-list li {
    display: flex;
    align-items: center;
    gap: 12px;
    white-space: nowrap;
  }
  .contact-icon {
    width: 17px;
    height: 17px;
    flex: none;
  }
  .brand-lockup {
    position: absolute;
    left: 560px;
    top: 210px;
    display: flex;
    align-items: center;
    gap: 18px;
  }
  .brand-dot {
    width: 74px;
    height: 74px;
    border-radius: 50%;
    background: var(--brand-blue);
  }
  .brand-name {
    font-size: 40px;
    font-weight: 600;
    color: var(--brand-blue);
    line-height: 1.05;
  }
</style>
</head>
<body>
  <div class="business-card">
    <svg class="card-shapes" viewBox="0 0 900 520" aria-hidden="true">
      <path d="M0,0 L455,0 C385,130 395,380 560,520 L0,520 Z" fill="var(--brand-blue)"/>
      <path d="M478,0 C405,135 420,385 610,520 L576,520 C410,385 400,130 466,0 Z" fill="var(--brand-pink)"/>
    </svg>

    <section class="contact-panel">
      <h1 class="person-name">Daniel Orvetto</h1>
      <p class="person-title">Director</p>

      <address class="office-address">
        027, 9th floor, Harbour<br>
        Lane HVN
      </address>

      <ul class="contact-list">
        <li>
          <svg class="contact-icon" viewBox="0 0 18 18"><rect x="5" y="1" width="8" height="16" rx="1.5" fill="none" stroke="currentColor" stroke-width="1.6"/><circle cx="9" cy="14.2" r="0.9" fill="currentColor"/></svg>
          013 482 5907
        </li>
        <li>
          <svg class="contact-icon" viewBox="0 0 18 18"><path d="M4,2 L7,2 L8,6 L6,7.5 C7,10 8,11 10.5,12 L12,10 L16,11 L16,14 C16,15 15,16 14,16 C8,16 2,10 2,4 C2,3 3,2 4,2 Z" fill="currentColor"/></svg>
          013 482 5916
        </li>
        <li>
          <svg class="contact-icon" viewBox="0 0 18 18"><rect x="1.5" y="4" width="15" height="10" rx="1" fill="currentColor"/><path d="M2,4.5 L9,10 L16,4.5" fill="none" stroke="var(--brand-blue)" stroke-width="1.4"/></svg>
          info@brolvaquincare.com.au
        </li>
        <li>
          <svg class="contact-icon" viewBox="0 0 18 18"><circle cx="9" cy="9" r="7.2" fill="none" stroke="currentColor" stroke-width="1.5"/><ellipse cx="9" cy="9" rx="3" ry="7.2" fill="none" stroke="currentColor" stroke-width="1.3"/><path d="M2,9 L16,9 M3.2,5.5 L14.8,5.5 M3.2,12.5 L14.8,12.5" stroke="currentColor" stroke-width="1.2"/></svg>
          www.brolvaquincare.com.au
        </li>
      </ul>
    </section>

    <div class="brand-lockup">
      <span class="brand-dot"></span>
      <span class="brand-name">Brolvaquin<br>Care</span>
    </div>
  </div>
</body>
</html>
```